Business Card & Email Signature Design || Upmarket + Luxury

Rima Vale Honey, a New Zealand Manuka Honey company needs a Business Card & Email Signature design.

Our logo's are attached in Gold & Black versions, feel free to be creative with how you use the logo and it's patterns in your design.

Style:
- Looking for an Elegant, Luxurious, Upmarket feel.
- Black/Matte Black Card, Gold Foil, UV Embossing

Information to Add:

- Logo
- Company Name: Rima Vale Honey
- Name: Martin Holloway
- Title: Creative Director
- Phone: +64 2815 96 417
- Email: martin@rimavalehoney.example.nz
- Website: www.rimavalehoney.example.nz

- Socials: ***For email Signature Only***
- Facebook: https://www.facebook.com/rimavalehoney/
- Instagram: https://www.instagram.com/rimavalehoney/

Target Market(s)

Asia/Europe Luxury, Upmarket

Contact Information for Business Card

- Logo
- Name: Martin Holloway
- Phone: +64 2815 96 417

Font styles to use
Other font styles liked:
• Champagne & Limousines (Attached)

Requirements
Must have
• Business Card & Email Signature Design.

Looking for a Sleek, Luxury, Upmarket Design.

```html
<!DOCTYPE html>
<html lang="en">
<head>
<meta charset="utf-8">
<title>Rima Vale Honey – Business Card</title>
<link href="https://fonts.googleapis.com/css2?family=Josefin+Sans:wght@300;400&display=swap" rel="stylesheet">
<style>
  :root {
    --bg: #1c1c1c;
    --card: #0f1112;
    --comb-light: #2a2c2e;
    --gold: #d8bf6e;
    --gold-light: #efe2a6;
    --gold-deep: #a88a3c;
    --ink: #f2f0ea;
  }
  * { box-sizing: border-box; margin: 0; padding: 0; }
  html, body {
    width: 1200px; height: 675px; overflow: hidden;
    background: var(--bg);
    font-family: "Josefin Sans", sans-serif;
  }
  .stage {
    position: relative; width: 1200px; height: 675px;
    display: flex; justify-content: center; align-items: center; gap: 80px;
  }
  .card {
    position: relative; width: 510px; height: 292px;
    background: var(--card); overflow: hidden;
  }
  .card-texture {
    position: absolute; inset: 0;
    background: radial-gradient(ellipse at 35% 20%, var(--comb-light) 0%, var(--card) 70%);
  }
  /* Front */
  .front-brand {
    position: absolute; left: 0; right: 0; top: 118px;
    text-align: center; color: var(--gold);
    font-weight: 400; font-size: 34px; letter-spacing: 6px; text-transform: uppercase;
  }
  .front-web {
    position: absolute; left: 0; right: 0; top: 186px;
    text-align: center; color: var(--ink);
    font-weight: 400; font-size: 15px; letter-spacing: 0.3px;
  }
  /* Back */
  .gold-band {
    position: absolute; left: 30px; top: 0; bottom: 0; width: 26px;
    background: linear-gradient(180deg, var(--gold-light), var(--gold-deep) 55%, var(--gold-light));
  }
  .seal {
    position: absolute; right: 22px; top: 16px;
    display: flex; align-items: center; gap: 6px;
    color: var(--gold); font-size: 11px; letter-spacing: 1px; text-transform: uppercase;
  }
  .seal-ring { width: 14px; height: 14px; border-radius: 50%; background: var(--gold); }
  .holder { position: absolute; left: 92px; top: 112px; }
  .holder-title {
    color: var(--gold); font-weight: 300; font-size: 15px;
    border-bottom: 1px solid var(--gold); display: inline-block; padding-bottom: 1px;
  }
  .holder-name {
    color: var(--ink); font-weight: 300; font-size: 34px;
    text-transform: uppercase; margin-top: 6px; letter-spacing: 0.5px;
  }
  .contact { position: absolute; left: 64px; top: 196px; }
  .contact-row {
    display: flex; align-items: center; gap: 12px; height: 27px;
    color: var(--ink); font-size: 14px; font-weight: 300;
  }
  .contact-row svg { width: 16px; height: 16px; flex: none; }
  .contact-row strong { font-weight: 400; }
</style>
</head>
<body>
<main class="stage">
  <section class="card card-front">
    <div class="card-texture" role="img" aria-label="Dark honeycomb pattern"></div>
    <div class="front-brand">Rima Vale Honey</div>
    <div class="front-web">www.rimavalehoney.example.nz</div>
  </section>

  <section class="card card-back">
    <div class="card-texture" role="img" aria-label="Dark honeycomb pattern"></div>
    <div class="gold-band"></div>
    <div class="seal"><span class="seal-ring"></span>Rima Vale Honey</div>
    <div class="holder">
      <div class="holder-title">Creative Director</div>
      <div class="holder-name">Martin Holloway</div>
    </div>
    <div class="contact">
      <div class="contact-row">
        <svg viewBox="0 0 24 24" fill="#111"><path d="M6.6 10.8a15.1 15.1 0 0 0 6.6 6.6l2.2-2.2c.3-.3.7-.4 1-.2 1.1.4 2.3.6 3.6.6.6 0 1 .4 1 1V20c0 .6-.4 1-1 1A17 17 0 0 1 3 4c0-.6.4-1 1-1h3.5c.6 0 1 .4 1 1 0 1.3.2 2.5.6 3.6.1.3 0 .7-.2 1z"/></svg>
        <span>Phone: <strong>+64 2815 96 417</strong></span>
      </div>
      <div class="contact-row">
        <svg viewBox="0 0 24 24" fill="none" stroke="#111" stroke-width="2"><rect x="3" y="5" width="18" height="14"/><path d="M3 5l9 8 9-8"/></svg>
        <span>Email: <strong>martin@rimavalehoney.example.nz</strong></span>
      </div>
    </div>
  </section>
</main>
</body>
</html>
```